Design website for new email startup

We are starting a company called Pingo.QZ (it will live at http://pingo.qz).

We would like the main landing page for our site designed. We have provided a very simple wireframe to help provide direction for the content it should include, but we do not expect the designers to adhere to it at all - we encourage unique ideas. There is some sample text in the wireframe - this does not have to be used, but may provide ideas.

We provide an easy way for people to manage email for a custom domain name. For example if you own "yourhouseword.example" you can point your DNS records to us and we'll make it easy to have emails addressed to your domain get forwarded to your existing email (gmail, etc). Folks running blogs, and other small sites can quickly setup email addresses for their domains and manage them in one place.

(For technical folks, we have you point your dns mx records to us, hence the name. That way all your email hits us and we can redirect it wherever you want. We make it easy to manage a single domain or a bunch of domains. Many domain registrars offer this service for a fee, and have clumsy management tools. We provide a robust simple toolset for free, as well as premium options).

The goal of the landing page is to get folks into the signup flow. The second priority flow is to have them take a look at the premium plan offerings.

We may offer the winning designer additional work for the remainder of the site design.
Updates

I've changed this project to a committed payment.  It is no longer refundable.  Thank you.

Target Market(s)

Bloggers, podcasters, designers, app developers - people who are a little tech savvy.

Industry/Entity Type

It Company

Font styles to use
Sans Serif

Colors

Designer to choose colors to be used in the design.

Requirements
Must have
• A full fidelity mockup (comp) of the landing page including the source file (psd, ai, etc).

Some sort of logo treatment for the pingo.qz brand

A call to action for signup, such as the suggested 'Get Started Here'
Nice to have
• A hip startup feel

Incorporation of the email theme

Give the impression it is simple, easy and fast

```html
<!DOCTYPE html>
<html lang="en">
<head>
<meta charset="utf-8">
<title>Pingo.QZ — Email for your domain</title>
<link href="https://fonts.googleapis.com/css2?family=Arimo:wght@400;700&display=swap" rel="stylesheet">
<style>
  :root {
    --brand-blue: #3aa8ec;
    --nav-text: #333333;
    --hero-dark: #2c3d4f;
    --hero-mid: #5d7288;
    --hero-light: #b9c8d6;
    --tick-green: #8dc63f;
    --button-top: #3fa2e6;
    --button-bottom: #1f7fcf;
    --button-border: #1a6fb6;
    --link-blue: #1b5d9b;
    --body-grey: #555555;
    --footer-bg: #9a9a9a;
    --white: #ffffff;
  }
  * { box-sizing: border-box; margin: 0; padding: 0; }
  html, body { width: 1200px; height: 826px; overflow: hidden; background: var(--white); }
  body { font-family: "Arimo", Arial, sans-serif; position: relative; }

  .site-header { position: absolute; left: 0; top: 0; width: 1200px; height: 76px; background: var(--white); }
  .brand { position: absolute; left: 173px; top: 22px; font-size: 27px; font-weight: 700; color: var(--brand-blue); letter-spacing: -0.5px; }
  .main-nav { position: absolute; top: 33px; left: 0; font-size: 12.5px; color: var(--nav-text); }
  .main-nav a { position: absolute; white-space: nowrap; color: inherit; text-decoration: none; }

  .hero { position: absolute; left: 0; top: 76px; width: 1200px; height: 468px; overflow: hidden;
    background: radial-gradient(ellipse 480px 360px at 760px 220px, var(--hero-light) 0%, var(--hero-mid) 45%, var(--hero-dark) 100%); }
  .hero-visual { position: absolute; left: 600px; top: 16px; width: 310px; height: 452px;
    background: linear-gradient(180deg, rgba(215,222,230,.55) 0%, rgba(190,200,212,.35) 100%); }
  .slider-arrow { position: absolute; top: 214px; }
  .slider-arrow.prev { left: 66px; }
  .slider-arrow.next { left: 1086px; }

  .benefits { position: absolute; left: 183px; top: 108px; list-style: none; color: var(--white); }
  .benefits li { position: relative; padding-left: 27px; font-size: 17px; line-height: 24px; margin-bottom: 14px; width: 420px; }
  .benefits li.lead { font-size: 20.5px; margin-bottom: 17px; }
  .benefits svg { position: absolute; left: 0; top: 4px; }

  .cta { position: absolute; top: 323px; height: 41px; width: 173px; display: flex; align-items: center; justify-content: center;
    color: var(--white); font-size: 13px; font-weight: 700; text-decoration: none; letter-spacing: .2px;
    background: linear-gradient(var(--button-top), var(--button-bottom)); border: 1px solid var(--button-border); border-radius: 2px; }
  .cta.signup { left: 213px; }
  .cta.plans { left: 410px; }

  .guide-visual { position: absolute; }
  .guide-title { position: absolute; font-size: 14px; line-height: 20.5px; color: var(--link-blue); width: 250px; text-decoration: none; }
  .guide-body { position: absolute; font-size: 10.5px; line-height: 19px; color: var(--body-grey); width: 250px; }
  .cloud-art { left: 175px; top: 591px; width: 152px; height: 107px; background: #cfe7f7; }
  .partner-name { position: absolute; left: 628px; top: 583px; width: 160px; height: 133px; display: flex; align-items: center; justify-content: center;
    font-size: 21px; font-weight: 700; color: #222222; }

  .site-footer { position: absolute; left: 0; top: 767px; width: 1200px; height: 59px; background: var(--footer-bg);
    color: var(--white); font-size: 9.5px; display: flex; align-items: center; justify-content: center; gap: 14px; }
</style>
</head>
<body>
  <header class="site-header">
    <div class="brand">Pingo.QZ</div>
    <nav class="main-nav">
      <a href="#" style="left:766px">How it works</a>
      <a href="#" style="left:894px">Support</a>
      <a href="#" style="left:996px">Login</a>
    </nav>
  </header>

  <section class="hero">
    <div class="hero-visual" role="img" aria-label="Photo of a hand touching an open envelope with an @ card"></div>

    <svg class="slider-arrow prev" width="48" height="48" viewBox="0 0 48 48" aria-label="Previous slide">
      <circle cx="24" cy="24" r="22" fill="none" stroke="rgba(255,255,255,.35)" stroke-width="2"/>
      <path d="M30 13 L14 24 L30 35 L25 24 Z" fill="rgba(255,255,255,.35)"/>
    </svg>
    <svg class="slider-arrow next" width="48" height="48" viewBox="0 0 48 48" aria-label="Next slide">
      <circle cx="24" cy="24" r="22" fill="none" stroke="rgba(255,255,255,.35)" stroke-width="2"/>
      <path d="M18 13 L34 24 L18 35 L23 24 Z" fill="rgba(255,255,255,.35)"/>
    </svg>

    <ul class="benefits">
      <li class="lead"><svg width="18" height="16" viewBox="0 0 18 16"><path d="M1 9 L6 14 L17 1" fill="none" stroke="var(--tick-green)" stroke-width="3"/></svg>We make email easy</li>
      <li><svg width="18" height="16" viewBox="0 0 18 16"><path d="M1 9 L6 14 L17 1" fill="none" stroke="var(--tick-green)" stroke-width="3"/></svg>Give us five minutes and well get you email from your domain</li>
      <li><svg width="18" height="16" viewBox="0 0 18 16"><path d="M1 9 L6 14 L17 1" fill="none" stroke="var(--tick-green)" stroke-width="3"/></svg>Easily forword mail from your custom domain name whereever you want it</li>
      <li><svg width="18" height="16" viewBox="0 0 18 16"><path d="M1 9 L6 14 L17 1" fill="none" stroke="var(--tick-green)" stroke-width="3"/></svg>You take the mail,we'll keep the spam</li>
    </ul>

    <a class="cta signup" href="#">GET STARTED HERE</a>
    <a class="cta plans" href="#">COMPARE PLANS</a>
  </section>

  <div class="guide-visual cloud-art" role="img" aria-label="Illustration of a cloud with a check mark"></div>
  <a class="guide-title" href="#" style="left:346px;top:592px;width:240px">How to configure your SkyShield DNS to use pingo.qz</a>
  <p class="guide-body" style="left:346px;top:645px">Lorem Ipsum is simply dummy text of the printing and typesetting industry. Lorem Ipsum has been the industry's standard dummy text ever since...</p>

  <div class="partner-name">NameHarbor</div>
  <a class="guide-title" href="#" style="left:801px;top:597px">Use Pingo.QZ with your NameHarbor Domain registration for reliable email forwarding</a>
  <p class="guide-body" style="left:801px;top:663px">Lorem Ipsum is simply dummy text of the printing and typesetting industry...</p>

  <footer class="site-footer">
    <span>© Copyright 2014. Pingo.QZ. All rights reserved. Privacy Policy</span>
    <span>|</span>
    <span>Terms &amp; Codition</span>
    <span>|</span>
    <span>Disclaimer</span>
  </footer>
</body>
</html>
```